Business Card for Field Bloom-Eco Friendly Organic Clothing Brand

We are looking for an amazing business card for our eco friendly, organic clothing brand. We are thinking maybe a business card with a peel off sticker on the back, since our hanging clothing tag is a peel off sticker on the back. I will attach our hang tag so we can make sure we stay in line with our design. I've also attached a bag we are doing because I do like the scattered emblem look as well.

```html
<!DOCTYPE html>
<html lang="en">
<head>
<meta charset="utf-8">
<title>Field Bloom – Business Card</title>
<link href="https://fonts.googleapis.com/css2?family=Open+Sans:wght@400;600;700&display=swap" rel="stylesheet">
<style>
  :root {
    --backdrop: #2e2a27;
    --card: #141414;
    --card-edge: #1d1d1d;
    --gold: #d9b23a;
    --gold-light: #f3d874;
    --gold-dark: #9c7a1c;
    --ink-light: #f2f2f2;
    --camo-dark: #23281b;
    --camo-olive: #6b6f3e;
  }
  * { margin: 0; padding: 0; box-sizing: border-box; }
  html, body {
    width: 1200px; height: 844px; overflow: hidden;
    background: var(--backdrop);
    font-family: "Open Sans", Arial, sans-serif;
  }
  .stage {
    position: relative; width: 1200px; height: 844px;
    display: flex; align-items: center; justify-content: center; gap: 60px;
  }
  .card {
    position: relative; width: 500px; height: 286px;
    background: linear-gradient(120deg, var(--card) 0%, var(--card-edge) 70%, #262626 100%);
    box-shadow: 0 14px 30px rgba(0,0,0,.45);
    overflow: hidden;
  }
  .gold-band {
    position: absolute; left: 0; right: 0; height: 9px;
    background: linear-gradient(90deg, var(--gold-dark), var(--gold-light) 40%, var(--gold) 70%, var(--gold-dark));
  }
  .gold-band--top { top: 14px; }
  .gold-band--bottom { bottom: 14px; }

  /* Front */
  .front__figure {
    position: absolute; left: 0; bottom: 23px; width: 150px; height: 200px;
    background: radial-gradient(ellipse at 40% 70%, #d8b23a 0%, #8a7f3c 45%, var(--camo-olive) 70%, rgba(60,62,40,0) 72%);
  }
  .front__identity {
    position: absolute; left: 210px; top: 78px; text-align: left;
  }
  .front__name {
    color: var(--gold); font-weight: 700; font-size: 15px; letter-spacing: .5px;
    padding-bottom: 3px; border-bottom: 1px solid var(--gold);
  }
  .front__title { color: var(--ink-light); font-size: 12px; margin-top: 2px; padding-left: 12px; }
  .front__contact {
    position: absolute; left: 230px; top: 162px; width: 190px;
    text-align: center; color: var(--ink-light); font-size: 13px; line-height: 17px;
  }

  /* Back */
  .back__tab {
    position: absolute; width: 18px; height: 36px;
    background: linear-gradient(180deg, var(--gold-light), var(--gold) 50%, var(--gold-dark));
  }
  .back__tab--left { left: 0; top: 150px; }
  .back__tab--right { right: 0; top: 22px; }
  .sticker {
    position: absolute; left: 150px; top: 100px; width: 230px; height: 86px;
    border: 3px solid var(--gold); border-radius: 8px;
    background: linear-gradient(135deg, var(--camo-dark), #30341f 50%, var(--camo-dark));
    display: flex; align-items: center; gap: 14px; padding-left: 20px;
  }
  .sticker__mark {
    width: 34px; height: 34px; background: var(--gold); flex: none;
  }
  .sticker__text { display: flex; flex-direction: column; }
  .sticker__name { color: var(--gold); font-weight: 700; font-size: 24px; line-height: 28px; }
  .sticker__url { color: var(--gold); font-size: 9px; margin-top: 2px; }
</style>
</head>
<body>
<main class="stage">
  <section class="card card--front" aria-label="Business card front">
    <div class="gold-band gold-band--top"></div>
    <div class="front__figure" role="img" aria-label="Camouflage-patterned silhouette of a person seated in a meditation pose"></div>
    <div class="front__identity">
      <p class="front__name">MARCUS HALE</p>
      <p class="front__title">Managing Director</p>
    </div>
    <div class="front__contact">
      <p>044-555-0192</p>
      <p>123-555-0147</p>
      <p>hello@fieldbloom.com</p>
      <p>www.fieldbloom.com</p>
    </div>
    <div class="gold-band gold-band--bottom"></div>
  </section>

  <section class="card card--back" aria-label="Business card back">
    <div class="back__tab back__tab--right"></div>
    <div class="back__tab back__tab--left"></div>
    <div class="sticker">
      <span class="sticker__mark"></span>
      <div class="sticker__text">
        <span class="sticker__name">Field Bloom</span>
        <span class="sticker__url">www.fieldbloom.com</span>
      </div>
    </div>
  </section>
</main>
</body>
</html>
```